Harbor Crestline (Business Card Design)

Need business cards designed. Something modern, chic, and sleek. Mabye the back of the card should be the navy blue that is in the logo and then just the logo on the back.

Target Market(s)

Those in the hotel, office, and renovation industry

Contact Information for Business Card

1. Logo 2. Dorian Fenwick 3. CEO/Founder 4. Phone: (833) HarbCre / (833) 427-2731 5. Email: dorian@theharborcrestline.com 6. Website: www.theharborcrestline.com

Font styles to use
Other font styles liked:
• Look at the logo font and base the font for everything else off of that.

Colors
0054AA
0677BA
7BADD7
CADEEF
E8F1F8

Requirements
Must have
• Colors that are associated in the logo
Nice to have
• Sleek modern clean and chic design.

```html
<!DOCTYPE html>
<html lang="en">
<head>
<meta charset="utf-8">
<title>Harbor Crestline – Business Card</title>
<link rel="stylesheet" href="https://fonts.googleapis.com/css2?family=Raleway:wght@500;600;700&display=swap">
<style>
  :root {
    --navy: #0b1842;
    --gold: #d4a64a;
    --white: #ffffff;
    --paper: #f7f7f7;
    --backdrop: #3a3a3a;
  }
  * { margin: 0; padding: 0; box-sizing: border-box; }
  html, body { width: 1200px; height: 1200px; overflow: hidden; }
  body {
    background: var(--backdrop);
    font-family: "Raleway", sans-serif;
    display: flex;
    flex-direction: column;
    align-items: center;
    justify-content: center;
    gap: 72px;
  }
  .card {
    position: relative;
    width: 840px;
    height: 480px;
    border-radius: 34px;
    overflow: hidden;
    box-shadow: 0 14px 30px rgba(0,0,0,0.4);
  }
  .card-front { background: linear-gradient(180deg, var(--white), var(--paper)); }
  .card-back { background: var(--navy); }
  .front-shape { position: absolute; inset: 0; }

  .wordmark {
    position: absolute;
    display: flex;
    align-items: center;
    font-weight: 700;
    letter-spacing: 0.08em;
    text-transform: uppercase;
    line-height: 1.1;
  }
  .wordmark-square { background: currentColor; flex: none; }
  .card-front .wordmark {
    color: var(--navy);
    left: 596px;
    top: 150px;
    font-size: 29px;
    gap: 12px;
  }
  .card-front .wordmark-square { width: 12px; height: 12px; }
  .card-back .wordmark {
    color: var(--white);
    left: 50%;
    top: 50%;
    transform: translate(-50%, -50%);
    font-size: 58px;
    gap: 18px;
  }
  .card-back .wordmark-square { width: 16px; height: 16px; }

  .contact { position: absolute; left: 56px; top: 190px; color: var(--white); }
  .contact-name { color: var(--gold); font-weight: 700; font-size: 30px; letter-spacing: 0.01em; text-transform: uppercase; }
  .contact-title { font-weight: 500; font-size: 20px; margin: 2px 0 16px; text-transform: uppercase; }
  .contact-list { list-style: none; font-size: 17px; font-weight: 500; }
  .contact-list li { display: flex; align-items: center; gap: 10px; margin-bottom: 8px; }
  .contact-icon { width: 20px; height: 20px; flex: none; }
</style>
</head>
<body>
  <section class="card card-front" aria-label="Card front">
    <svg class="front-shape" viewBox="0 0 840 480" preserveAspectRatio="none" aria-hidden="true">
      <polygon points="0,0 380,0 530,190 490,480 0,480" fill="var(--navy)"/>
      <polyline points="394,0 544,190 506,480" fill="none" stroke="var(--white)" stroke-width="8"/>
      <polyline points="404,0 556,190 518,480" fill="none" stroke="var(--gold)" stroke-width="9"/>
    </svg>
    <div class="wordmark"><span class="wordmark-square"></span><span>Harbor<br>Crestline</span></div>
    <div class="contact">
      <p class="contact-name">Dorian Fenwick</p>
      <p class="contact-title">CEO | Founder</p>
      <ul class="contact-list">
        <li>
          <svg class="contact-icon" viewBox="0 0 24 24"><path fill="var(--gold)" d="M6.6 10.8a15 15 0 0 0 6.6 6.6l2.2-2.2c.3-.3.7-.4 1-.2 1.1.4 2.3.6 3.6.6.6 0 1 .4 1 1V20c0 .6-.4 1-1 1A17 17 0 0 1 3 4c0-.6.4-1 1-1h3.5c.6 0 1 .4 1 1 0 1.3.2 2.5.6 3.6.1.3 0 .7-.2 1z"/></svg>
          <span>(833) HarbCre | (833) 427-2731</span>
        </li>
        <li>
          <svg class="contact-icon" viewBox="0 0 24 24"><rect x="2" y="5" width="20" height="14" rx="1" fill="var(--gold)"/><path d="M2 6l10 7 10-7" fill="none" stroke="var(--navy)" stroke-width="1.6"/></svg>
          <span>dorian@theharborcrestline.com</span>
        </li>
        <li>
          <svg class="contact-icon" viewBox="0 0 24 24" fill="none" stroke="var(--gold)" stroke-width="1.8"><circle cx="12" cy="12" r="9"/><ellipse cx="12" cy="12" rx="4" ry="9"/><path d="M3 12h18M5 7h14M5 17h14"/></svg>
          <span>www.theharborcrestline.com</span>
        </li>
      </ul>
    </div>
  </section>

  <section class="card card-back" aria-label="Card back">
    <div class="wordmark"><span class="wordmark-square"></span><span>Harbor<br>Crestline</span></div>
  </section>
</body>
</html>
```